Redesign Website - Current one too plain

The description is in the uploaded file. Please let me know if you need any more information. I'd prefer it if someone could implement the design to a WordPress site but the best design will win, regardless.
I would like the forms to look nice as well
UPDATE:
I don't think we can use the images that I provided, I think they make the site look a bit 'cheap' and I really don't know how to replace them. One thought I have had is to make the "Simple, Unique, Effective" a second feature on the right side of the page with the search on the left
Target Market(s)
Small companies, private sellers of cars and people who rent their caravan/holiday home out
Industry/Entity Type
Advertising
Number of Pages Required
3 page
Colors
Designer to choose colors to be used in the design.
Look and feel
Each slider illustrates characteristics of the customer's brand and the style your logo design should communicate.

```html
<!DOCTYPE html>
<html lang="en">
<head>
<meta charset="utf-8">
<title>KODRA – Discover And Connect</title>
<link rel="stylesheet" href="https://fonts.googleapis.com/css2?family=Inter:wght@400;500;600;700&display=swap">
<style>
  :root {
    --ink: #222222;
    --lime: #eafb4f;
    --white: #ffffff;
    --text-dark: #1a1a1a;
    --car-light: #9a9ca3;
    --car-mid: #55585f;
    --car-dark: #2a2b2f;
  }
  * { box-sizing: border-box; margin: 0; padding: 0; }
  html, body { width: 1200px; height: 2513px; overflow: hidden; }
  body {
    position: relative;
    background: var(--ink);
    color: var(--white);
    font-family: "Inter", Arial, sans-serif;
  }
  .abs { position: absolute; }

  /* Header */
  .brand { left: 57px; top: 48px; display: flex; align-items: center; gap: 12px; }
  .brand-dot { width: 26px; height: 26px; border-radius: 50%; background: var(--lime); }
  .brand-name { color: var(--lime); font-size: 26px; font-weight: 500; letter-spacing: 0.5px; }
  .main-nav { left: 438px; top: 66px; display: flex; font-size: 13px; font-weight: 500; }
  .main-nav a { color: var(--white); text-decoration: none; }
  .main-nav a:nth-child(1) { margin-right: 39px; }
  .main-nav a:nth-child(2) { margin-right: 44px; }
  .main-nav a:nth-child(3) { margin-right: 55px; }
  .btn-login {
    left: 1006px; top: 58px; width: 137px; height: 37px; border-radius: 19px;
    background: var(--lime); color: var(--ink); font-size: 17px; font-weight: 500;
    display: flex; align-items: center; justify-content: center;
  }

  /* Hero */
  .hero-title { left: 0; width: 1200px; top: 138px; text-align: center; font-size: 60px; font-weight: 600; letter-spacing: 0.3px; }
  .hero-sub { left: 0; width: 1200px; top: 223px; text-align: center; font-size: 16.5px; }
  .code-char {
    top: 306px; width: 80px; margin-left: -40px; text-align: center;
    color: var(--lime); font-size: 80px; font-weight: 500; line-height: 1;
  }
  .chevron { width: 17px; height: 17px; margin-left: -8.5px; }
  .chip {
    top: 439px; height: 33px; border: 1.5px solid var(--lime); border-radius: 17px;
    color: var(--lime); font-size: 17px; display: flex; align-items: center; justify-content: center;
  }
  .btn-search {
    left: 481px; top: 500px; width: 237px; height: 36px; border-radius: 18px;
    background: var(--lime); color: var(--ink); font-size: 17px; font-weight: 500;
    display: flex; align-items: center; justify-content: center;
  }
  .hero-photo {
    left: 0; top: 573px; width: 1200px; height: 780px;
    background:
      radial-gradient(ellipse 52% 40% at 50% 30%, var(--car-mid) 0%, var(--car-dark) 70%, transparent 100%),
      radial-gradient(ellipse 60% 55% at 50% 55%, var(--car-light) 0%, var(--car-mid) 45%, var(--ink) 85%);
    border-radius: 50% 50% 0 0 / 22% 22% 0 0;
  }

  /* About */
  .about-panel { left: 57px; top: 963px; width: 1086px; height: 479px; background: var(--white); border-radius: 30px; }
  .about-title { left: 0; width: 1200px; top: 1024px; text-align: center; color: var(--text-dark); font-size: 26px; font-weight: 600; }
  .feature-card {
    top: 1116px; width: 266px; height: 266px; border-radius: 30px; background: var(--ink);
    text-align: center;
  }
  .feature-icon { position: absolute; left: 93px; top: 50px; width: 80px; height: 80px; }
  .feature-name { position: absolute; left: 0; width: 100%; top: 150px; color: var(--lime); font-size: 22px; font-weight: 600; }
  .feature-text { position: absolute; left: 30px; right: 30px; top: 186px; font-size: 13.5px; line-height: 16px; }

  /* How it works */
  .section-title { left: 0; width: 1200px; text-align: center; font-size: 26px; font-weight: 600; }
  .how-title { top: 1504px; color: var(--lime); }
  .steps { left: 83px; top: 1578px; width: 470px; font-size: 16.5px; line-height: 28.5px; }
  .steps p { margin-bottom: 28px; }

  /* Why choose us */
  .why-band { left: 0; top: 2116px; width: 1200px; height: 397px; background: var(--lime); color: var(--text-dark); }
  .why-title { top: 50px; }
  .why-body { position: absolute; left: 72px; top: 139px; width: 1060px; font-size: 16.5px; line-height: 28.5px; }
  .why-body ul { padding-left: 25px; }
</style>
</head>
<body>
  <header>
    <div class="abs brand"><span class="brand-dot"></span><span class="brand-name">KODRA</span></div>
    <nav class="abs main-nav">
      <a href="#">Home</a><a href="#">Advertise</a><a href="#">Contact</a><a href="#">Register</a>
    </nav>
    <a class="abs btn-login">Login</a>
  </header>

  <section class="hero">
    <h1 class="abs hero-title">Discover And Connect</h1>
    <p class="abs hero-sub">Display Your Unique Code on Your Vehicle to Attract Customers</p>

    <svg class="abs chevron" style="left:546px;top:292px" viewBox="0 0 17 17"><circle cx="8.5" cy="8.5" r="8.5" fill="#eafb4f"/><path d="M4.5 10.5 L8.5 6.5 L12.5 10.5" stroke="#222" stroke-width="1.8" fill="none"/></svg>
    <svg class="abs chevron" style="left:631px;top:292px" viewBox="0 0 17 17"><circle cx="8.5" cy="8.5" r="8.5" fill="#eafb4f"/><path d="M4.5 10.5 L8.5 6.5 L12.5 10.5" stroke="#222" stroke-width="1.8" fill="none"/></svg>
    <div class="abs code-char" style="left:546px">S</div>
    <div class="abs code-char" style="left:631px">6</div>
    <svg class="abs chevron" style="left:546px;top:393px" viewBox="0 0 17 17"><circle cx="8.5" cy="8.5" r="8.5" fill="#eafb4f"/><path d="M4.5 6.5 L8.5 10.5 L12.5 6.5" stroke="#222" stroke-width="1.8" fill="none"/></svg>
    <svg class="abs chevron" style="left:631px;top:393px" viewBox="0 0 17 17"><circle cx="8.5" cy="8.5" r="8.5" fill="#eafb4f"/><path d="M4.5 6.5 L8.5 10.5 L12.5 6.5" stroke="#222" stroke-width="1.8" fill="none"/></svg>

    <span class="abs chip" style="left:439px;width:55px">Car</span>
    <span class="abs chip" style="left:529px;width:93px">Caravan</span>
    <span class="abs chip" style="left:658px;width:102px">Company</span>
    <a class="abs btn-search">Search</a>

    <div class="abs hero-photo" role="img" aria-label="Front view of a dark grey sports car"></div>
  </section>

  <section class="about">
    <div class="abs about-panel"></div>
    <h2 class="abs about-title">About us</h2>

    <article class="abs feature-card" style="left:134px">
      <svg class="feature-icon" viewBox="0 0 80 80" fill="none" stroke="#eafb4f" stroke-width="2.5" stroke-linecap="round">
        <path d="M30 72 V48 L26 36 L34 34 L36 22 Q40 16 44 22 V34 L52 36 L50 58 L44 72"/>
        <path d="M30 8 L32 14 M22 14 L27 18 M40 6 V12"/>
      </svg>
      <h3 class="feature-name">Simple</h3>
      <p class="feature-text">Create your advert and display your code</p>
    </article>

    <article class="abs feature-card" style="left:467px">
      <svg class="feature-icon" viewBox="0 0 80 80" fill="none" stroke="#eafb4f" stroke-width="2.5" stroke-linecap="round">
        <circle cx="32" cy="34" r="22"/>
        <circle cx="46" cy="46" r="14"/>
        <path d="M56 56 L70 70"/>
      </svg>
      <h3 class="feature-name">Unique</h3>
      <p class="feature-text">Customers find you by an easy-to-remember code</p>
    </article>

    <article class="abs feature-card" style="left:800px">
      <svg class="feature-icon" viewBox="0 0 80 80" fill="none" stroke="#eafb4f" stroke-width="2.5" stroke-linecap="round">
        <circle cx="40" cy="40" r="36"/>
        <circle cx="40" cy="40" r="22"/>
        <circle cx="40" cy="40" r="13"/>
        <path d="M40 32 V40 L46 44"/>
      </svg>
      <h3 class="feature-name">Effective</h3>
      <p class="feature-text">Customers are directed to you and not a list of your competitors</p>
    </article>
  </section>

  <section class="how">
    <h2 class="abs section-title how-title">How it works</h2>
    <div class="abs steps">
      <p>Step 1: Create Your Advert Content: Generate your unique code and create an eye-catching advert that showcases your business. Highlight your products, services, and contact details to ensure customers can easily reach you.</p>
      <p>Step 2: Display Your Code Content: Affix your code prominently on your vehicles. Whether it's a car, van, or caravan, your code will act as a beacon, guiding interested customers right to your doorstep.</p>
      <p>Step 3: Customers Find You Content: Sit back and watch as customers effortlessly find and connect with your business using your memorable code. Increase your visibility and enhance your customer base with our innovative concept.</p>
    </div>
  </section>

  <section class="abs why-band">
    <h2 class="abs section-title why-title">Why Choose Us</h2>
    <div class="why-body">
      <p>Our platform offers a user-friendly experience that empowers businesses of all sizes to increase their presence. With our easy-to-use system and eye-catching codes, you can enjoy these benefits:</p>
      <ul>
        <li>Stand out from competitors with a unique identifier</li>
        <li>Attract more customers with straightforward access to your business</li>
        <li>Increase your brand recognition and credibility</li>
        <li>Track the effectiveness of your adverts with real-time data</li>
      </ul>
    </div>
  </section>
</body>
</html>
```